Business card for dental office with laser therapy / dental facial esthetic

A simple logo which should signifies
Dentistry intraoral as primary and with extended extraoral cosmetic facial esthetic services ( regenerative skincare ) which enhance Beauty as whole .
Conservative high tech approach by using laser intraoral and extraoral limited to face and neck
Front Face :May be black background with neon blue / purplish Rim signifies laser ( ?) & abstract face profile and tooth or Apple design in one ? / see upload inspiration design
Back side : simple appointment slots with date and time / white background / black letter

Color : black/ neon blue/ purplish and gold incorporate for logo design
Final design : dental / esthetic / modern high tech and safe

Target Market(s)

Dental Patients who seeks more high end cosmetic treatment

Industry/Entity Type

Health Care

Contact Information for Business Card

Esthetic modern elegant looking
Logo and office must haves important informations

Logo Text

Family & Cosmetic Dentistry

Font styles to use
Script

Requirements
Must have
• Name of practice and all important informations
• Family & Cosmetic Dentistry
• Lan B. Orsova DMD,PC
• 48302 Bramcote Lane ,ste.217
• Kettle Ridge ,VA 20931
• Ph. 555-308-7291
• Fax 555-3087295
Nice to have
• More abstract
• Front : black back ground with neon blue rim (signifies laser therapy)
• Logo can also be golden gold / neon blue
• Address & Infos can be white
Should not have
• Not to busy looking

```html
<!DOCTYPE html>
<html lang="en">
<head>
<meta charset="utf-8">
<title>Family &amp; Cosmetic Dentistry – Business Card</title>
<link rel="stylesheet" href="https://fonts.googleapis.com/css2?family=Montserrat:wght@600;700&family=Roboto:wght@400;500;700&display=swap">
<style>
  :root {
    --page: #e9e6e1;
    --card-white: #ffffff;
    --ink: #1a1a1a;
    --dots: #555555;
    --faint: #ececec;
    --card-black: #0b0c0e;
    --card-black-2: #1a1d22;
    --gold: #d2a644;
    --gold-deep: #a9802c;
    --neon: #7fd3f2;
    --neon-soft: #2e6f8c;
    --info: #8fc3e6;
  }
  * { box-sizing: border-box; margin: 0; padding: 0; }
  html, body { width: 1200px; height: 800px; overflow: hidden; }
  body {
    background: var(--page);
    position: relative;
  }
  .card {
    position: absolute;
    top: 245px;
    width: 540px;
    height: 309px;
    border-radius: 4px;
    overflow: hidden;
    box-shadow: 0 10px 28px rgba(0,0,0,0.18);
  }

  /* ---------- Appointment side ---------- */
  .card--appointment {
    left: 40px;
    background: var(--card-white);
    font-family: "Montserrat", sans-serif;
    color: var(--ink);
  }
  .appointment__mark {
    position: absolute;
    left: 150px;
    top: 20px;
    width: 260px;
    height: 260px;
    border-radius: 50%;
    background: var(--faint);
  }
  .appointment__title {
    position: absolute;
    top: 62px;
    left: 0;
    width: 100%;
    text-align: center;
    font-size: 13px;
    font-weight: 700;
    letter-spacing: 2px;
  }
  .appointment__rows {
    position: absolute;
    left: 44px;
    right: 40px;
    top: 100px;
    display: grid;
    grid-template-columns: 1fr 1fr;
    row-gap: 28px;
    column-gap: 28px;
  }
  .slot {
    display: flex;
    align-items: flex-end;
    font-size: 12px;
    font-weight: 700;
    letter-spacing: 1.5px;
  }
  .slot__line {
    flex: 1;
    margin-left: 6px;
    margin-bottom: 3px;
    border-bottom: 2px dotted var(--dots);
  }

  /* ---------- Contact side ---------- */
  .card--contact {
    left: 620px;
    background: radial-gradient(ellipse at 30% 40%, var(--card-black-2) 0%, var(--card-black) 70%);
    font-family: "Roboto", sans-serif;
  }
  .contact__pattern {
    position: absolute;
    right: 0;
    top: 0;
    width: 230px;
    height: 100%;
    background: radial-gradient(ellipse at 100% 55%, rgba(127,211,242,0.55) 0%, rgba(46,111,140,0.35) 40%, rgba(11,12,14,0) 75%);
  }
  .brand {
    position: absolute;
    left: 34px;
    top: 42px;
    display: flex;
    align-items: center;
    gap: 16px;
  }
  .brand__ring {
    width: 58px;
    height: 58px;
    border-radius: 50%;
    border: 3px solid var(--neon);
    flex: none;
  }
  .brand__name {
    color: var(--gold);
    font-weight: 500;
    font-size: 25px;
    line-height: 1.1;
    letter-spacing: 0.5px;
  }
  .contact__name {
    position: absolute;
    left: 36px;
    top: 142px;
    color: var(--gold);
    font-weight: 700;
    font-size: 17px;
  }
  .contact__list {
    position: absolute;
    left: 36px;
    top: 178px;
    list-style: none;
    color: var(--info);
    font-size: 13.5px;
  }
  .contact__item {
    display: flex;
    align-items: flex-start;
    gap: 10px;
    margin-bottom: 11px;
    line-height: 1.3;
  }
  .contact__icon {
    width: 18px;
    height: 18px;
    flex: none;
  }
</style>
</head>
<body>

  <section class="card card--appointment" aria-label="Appointment card">
    <div class="appointment__mark" aria-hidden="true"></div>
    <h2 class="appointment__title">APPOINTMENT</h2>
    <div class="appointment__rows">
      <div class="slot">DATE:<span class="slot__line"></span></div>
      <div class="slot">TIME:<span class="slot__line"></span></div>
      <div class="slot">DATE:<span class="slot__line"></span></div>
      <div class="slot">TIME:<span class="slot__line"></span></div>
      <div class="slot">DATE:<span class="slot__line"></span></div>
      <div class="slot">TIME:<span class="slot__line"></span></div>
      <div class="slot">DATE:<span class="slot__line"></span></div>
      <div class="slot">TIME:<span class="slot__line"></span></div>
    </div>
  </section>

  <section class="card card--contact" aria-label="Contact card">
    <div class="contact__pattern" role="img" aria-label="Glowing neon blue dot pattern"></div>

    <div class="brand">
      <span class="brand__ring" aria-hidden="true"></span>
      <span class="brand__name">Family &amp; Cosmetic<br>Dentistry</span>
    </div>

    <p class="contact__name">Lan B. Orsova DMD,PC</p>

    <ul class="contact__list">
      <li class="contact__item">
        <svg class="contact__icon" viewBox="0 0 18 18" aria-label="Phone">
          <circle cx="9" cy="9" r="9" fill="var(--gold-deep)"/>
          <path d="M6 4.5 L7.6 4.5 L8.2 7 L7.2 7.8 Q8 9.8 10.2 10.8 L11 9.8 L13.5 10.4 L13.5 12 Q13.5 13.3 12 13.3 Q5 12.6 4.7 6 Q4.7 4.5 6 4.5 Z" fill="var(--card-black)"/>
        </svg>
        <span>555-308-7291</span>
      </li>
      <li class="contact__item">
        <svg class="contact__icon" viewBox="0 0 18 18" aria-label="Fax">
          <circle cx="9" cy="9" r="9" fill="var(--gold-deep)"/>
          <rect x="6" y="4.5" width="6" height="3.5" fill="var(--card-black)"/>
          <rect x="4.5" y="8" width="9" height="4.5" rx="1" fill="var(--card-black)"/>
          <rect x="6.5" y="10.5" width="5" height="3" fill="var(--gold-deep)" stroke="var(--card-black)" stroke-width="0.8"/>
        </svg>
        <span>555-3087295</span>
      </li>
      <li class="contact__item">
        <svg class="contact__icon" viewBox="0 0 18 18" aria-label="Address">
          <circle cx="9" cy="9" r="9" fill="var(--gold-deep)"/>
          <path d="M9 4 A3.4 3.4 0 0 1 12.4 7.4 Q12.4 9.8 9 14 Q5.6 9.8 5.6 7.4 A3.4 3.4 0 0 1 9 4 Z" fill="var(--card-black)"/>
          <circle cx="9" cy="7.4" r="1.3" fill="var(--gold-deep)"/>
        </svg>
        <span>48302 Bramcote Lane ,ste.217<br>Kettle Ridge ,VA 20931</span>
      </li>
    </ul>
  </section>

</body>
</html>
```